VIP Card Design Project

uZorvo is a premium sneaker store selling brand name sneakers like Volta, Rexa, Kembro and etc. ( www.uzorvoshop.com ) We need to design a VIP card to promote one of our discount program called "Uzorvo VIP Band 17", which offers 24% discount off all full-priced items. The idea is because we have a "Peakline Gym center" (peaklinegym.com) next door and we are trying to design a discount program for people going to the fitness center.
The design is for the front of the card. The back will be black and white with benefits information and member information.
The front design need to include our logo, "VIP", "Band 17" and our web address "Uzorvo.com" and Chatterly and quibbr logo.
It will be a plastic card in the size of 3.375x2.125 (bleed size 3.5x2.25)

```html
<!DOCTYPE html>
<html lang="en">
<head>
<meta charset="utf-8">
<title>uZorvo VIP Band 17 Card</title>
<link href="https://fonts.googleapis.com/css2?family=Open+Sans:wght@400;600;700;800&family=Cinzel:wght@500&display=swap" rel="stylesheet">
<style>
  :root {
    --bg: #ece8e2;
    --card: #ffffff;
    --green: #3f9c35;
    --green-light: #8cc63f;
    --green-dark: #1f6a25;
    --green-text: #2e8a35;
    --orange: #f15a24;
    --orange-soft: #f7a21b;
    --ink: #1a1a1a;
    --social-a: #3b5998;
    --social-b: #55acee;
  }
  html, body {
    margin: 0;
    width: 1070px;
    height: 1200px;
    overflow: hidden;
    background: var(--bg);
  }
  .canvas { position: relative; width: 1070px; height: 1200px; }
  .card {
    position: absolute;
    left: 123px;
    width: 825px;
    height: 521px;
    background: var(--card);
    border-radius: 30px;
    overflow: hidden;
    box-shadow: 0 4px 14px rgba(0,0,0,.18);
  }
  .card-front { top: 52px; }
  .card-back { top: 626px; }
  .card svg { display: block; width: 825px; height: 521px; }
  .sans { font-family: "Open Sans", Arial, sans-serif; }
  .serif-caps { font-family: "Cinzel", Georgia, serif; }
  .brand-name { font-weight: 800; fill: var(--green); font-size: 88px; }
  .club-line { font-weight: 700; fill: var(--ink); font-size: 27px; }
  .club-number { font-weight: 700; fill: var(--orange); font-size: 80px; }
  .discount-text { fill: var(--green-dark); font-size: 21px; }
  .web-address { fill: var(--ink); font-size: 19px; }
  .social-name { font-weight: 700; font-size: 9px; fill: #fff; }
  .benefits-title { font-weight: 700; fill: #fff; font-size: 23px; }
  .benefits-intro { font-weight: 700; fill: var(--green-dark); font-size: 14.5px; }
  .benefit { fill: var(--green-text); font-size: 14px; }
  .field-label { font-weight: 700; font-size: 14.5px; }
  .field-name { fill: var(--green-dark); }
  .field-id { fill: var(--orange-soft); }
</style>
</head>
<body>
<main class="canvas">

  <section class="card card-front" aria-label="Card front">
    <svg viewBox="0 0 672 424" xmlns="http://www.w3.org/2000/svg">
      <defs>
        <linearGradient id="band-fill" x1="0" x2="1" y1="0" y2="0">
          <stop offset="0" stop-color="#ffffff"/>
          <stop offset="0.25" stop-color="#8cc63f"/>
          <stop offset="1" stop-color="#1f6a25"/>
        </linearGradient>
        <radialGradient id="badge-fill">
          <stop offset="0" stop-color="#fbb03b"/>
          <stop offset="1" stop-color="#f15a24" stop-opacity="0.2"/>
        </radialGradient>
      </defs>

      <g class="swoosh">
        <path d="M98 0 C 40 60, 20 150, 30 250 C 38 330, 48 380, 55 424 L 62 424 C 56 370, 60 300, 70 230 C 82 140, 110 60, 112 0 Z" fill="var(--green)"/>
        <path d="M405 0 C 430 80, 470 170, 560 190 C 610 200, 650 195, 672 188 L 672 205 C 640 215, 600 220, 560 212 C 470 195, 425 110, 398 0 Z" fill="var(--green)"/>
      </g>

      <text class="sans brand-name" x="138" y="196">uZorvo</text>

      <text class="sans club-line" x="573" y="54" text-anchor="middle">uzorvo</text>
      <text class="sans club-line" x="573" y="92" text-anchor="middle">VIP Band</text>
      <text class="sans club-number" x="573" y="176" text-anchor="middle">17</text>

      <g class="product-photos" stroke="var(--green)" stroke-width="2">
        <rect role="img" aria-label="Photo of a white and red basketball sneaker" x="192" y="243" width="122" height="88" rx="38" fill="#c9cdd2"/>
        <rect role="img" aria-label="Photo of a white sneaker with green stripes" x="333" y="243" width="120" height="88" rx="38" fill="#b8b3ab"/>
        <rect role="img" aria-label="Photo of a black and yellow low-top sneaker" x="470" y="243" width="121" height="88" rx="38" fill="#4a4a3a"/>
      </g>

      <rect x="148" y="340" width="524" height="40" fill="url(#band-fill)"/>
      <text class="serif-caps discount-text" x="388" y="368" text-anchor="middle">DISCOUNT OFF ALL FULL-PRICED ITEMS</text>

      <circle role="img" aria-label="Orange 24 percent discount badge" cx="145" cy="338" r="38" fill="url(#badge-fill)"/>

      <text class="sans web-address" x="320" y="408" text-anchor="middle">www.uzorvoshop.com</text>

      <g class="social">
        <rect x="530" y="390" width="38" height="20" rx="3" fill="var(--social-a)"/>
        <text class="sans social-name" x="549" y="403" text-anchor="middle">Chatterly</text>
        <rect x="572" y="390" width="34" height="20" rx="3" fill="var(--social-b)"/>
        <text class="sans social-name" x="589" y="403" text-anchor="middle">quibbr</text>
      </g>
    </svg>
  </section>

  <section class="card card-back" aria-label="Card back">
    <svg viewBox="0 0 672 424" xmlns="http://www.w3.org/2000/svg">
      <rect x="448" y="33" width="224" height="40" fill="var(--green-dark)"/>
      <rect x="444" y="33" width="4" height="40" fill="var(--green-light)"/>
      <text class="sans benefits-title" x="458" y="62">uzorvo Benefits</text>

      <text class="sans benefits-intro" x="33" y="104">The UZORVO Member Program entitles Members to the following benefits:</text>

      <g class="sans benefit">
        <text x="33" y="142">a.&#160;&#160;&#160;&#160;20% OFF your entire first purchase after you sign up (Limited Time Offer).</text>
        <text x="58" y="164">Certain items are excluded from this offer. Please see stores for details.</text>

        <text x="33" y="202">b.&#160;&#160;&#160;10% OFF every purchase while being a member.</text>
        <text x="58" y="224">Certain items are excluded from this offer. Please see stores for details.</text>

        <text x="33" y="258">c.&#160;&#160;&#160;&#160;Additional 10% OFF and FREE SHIPPING when an item is out of stock</text>
        <text x="60" y="280">in store but can be shipped to you from another location.</text>

        <text x="33" y="317">d.&#160;&#160;&#160;Eligible to purchase exclusive items offered to members only.</text>
        <text x="60" y="339">Purchasing of exclusive items is limited to 1 item per member per 30 days.</text>
        <text x="60" y="361">Please see stores for details.</text>
      </g>

      <text class="sans field-label field-name" x="35" y="402">Member Name :</text>
      <line x1="156" y1="403" x2="400" y2="403" stroke="var(--green-dark)" stroke-width="1.2"/>
      <text class="sans field-label field-id" x="418" y="402">Member ID :</text>
      <line x1="510" y1="403" x2="643" y2="403" stroke="var(--green-dark)" stroke-width="1.2"/>
    </svg>
  </section>

</main>
</body>
</html>
```